Antibacterial Hand Wash Squeeze Tube Label

We're looking for a contemporary label design for a new Antibacterial Hand Wash for an 8oz squeeze tube. The new consumer brand will be sold to consumers in major US retail stores & online. The moisturizing hand wash contains Aloe Vera, vitamin E, and other natural ingredients so the design should include the color green. Real photos are very effective on packaging, so a picture of Aloe Vera or possibly two hands washing would help draw consumers' attention to the tube on the retail shelf. The front label may wrap around the sides. Rear must be left mostly blank
Target Market(s)
US Consumers - retail stores & online
Industry/Entity Type
Consumer

```html
<!DOCTYPE html>
<html lang="en">
<head>
<meta charset="utf-8">
<title>Verdance Natural Hand Wash – Tube Labels</title>
<link rel="stylesheet" href="https://fonts.googleapis.com/css2?family=Montserrat:wght@600&family=Dancing+Script:wght@500&family=Cormorant+Garamond:wght@600&family=Oswald:wght@500&family=Roboto+Condensed:wght@400&display=swap">
<style>
  :root {
    --canvas: #f1f1f1;
    --label: #ffffff;
    --brand-green: #3fae3a;
    --band-green: #78a22f;
    --text-grey: #5a5a5a;
    --rule-grey: #b8b8b8;
    --aloe-light: #9fd46a;
    --aloe-dark: #2f8a2a;
    --skin: #e8b89a;
    --water: #bfe3f2;
  }
  * { margin: 0; padding: 0; box-sizing: border-box; }
  html, body { width: 1200px; height: 845px; overflow: hidden; }
  body { background: var(--canvas); position: relative; }

  .label {
    position: absolute;
    top: 100px;
    width: 278px;
    height: 530px;
    background: var(--label);
    box-shadow: 0 2px 10px rgba(0,0,0,0.06);
  }
  .label--front { left: 270px; }
  .label--alt { left: 638px; }

  /* Front label */
  .brand-name {
    position: absolute; left: 0; right: 0; top: 108px;
    text-align: center;
    font-family: "Montserrat", sans-serif; font-weight: 600;
    font-size: 48px; color: var(--brand-green); letter-spacing: -0.5px;
  }
  .subtitle {
    position: absolute; left: 0; right: 0; top: 174px;
    text-align: center;
    font-family: "Dancing Script", cursive; font-size: 19px;
    color: var(--text-grey);
  }
  .photo {
    position: absolute;
  }
  .photo--aloe-hands {
    left: 70px; top: 205px; width: 140px; height: 215px;
    background: linear-gradient(180deg, var(--aloe-light) 0%, var(--aloe-dark) 45%, var(--water) 62%, var(--skin) 100%);
    border-radius: 40px 40px 20px 20px;
    opacity: 0.85;
  }
  .claims {
    position: absolute; left: 0; right: 0; top: 448px;
    text-align: center;
    font-family: "Roboto Condensed", sans-serif; font-size: 11.5px;
    color: var(--text-grey); line-height: 15px;
  }
  .claims .rule {
    display: block; width: 36px; height: 1px; background: var(--rule-grey);
    margin: 0 auto 6px;
  }
  .claims .rule--wide { width: 88px; margin: 3px auto 0; }
  .claims .claim--green { color: var(--band-green); }
  .net-weight {
    position: absolute; left: 0; right: 0; top: 502px;
    text-align: center;
    font-family: "Roboto Condensed", sans-serif; font-size: 10px;
    color: #333;
  }

  /* Alternate label */
  .photo--aloe-fan {
    left: 28px; top: 148px; width: 228px; height: 176px;
    background: radial-gradient(ellipse at 50% 90%, var(--aloe-dark) 0%, var(--aloe-light) 55%, rgba(159,212,106,0) 72%);
  }
  .band {
    position: absolute; left: 95px; top: 0; width: 92px; height: 372px;
    background: var(--band-green);
    display: flex; align-items: center; justify-content: center;
  }
  .band-name {
    writing-mode: vertical-rl; transform: rotate(180deg);
    font-family: "Cormorant Garamond", serif; font-weight: 600;
    font-size: 60px; color: #ffffff; letter-spacing: 1px; line-height: 1;
  }
  .alt-natural {
    position: absolute; left: 0; right: 0; top: 376px;
    text-align: center;
    font-family: "Dancing Script", cursive; font-size: 19px; color: var(--text-grey);
  }
  .alt-product {
    position: absolute; left: 0; right: 0; top: 398px;
    text-align: center;
    font-family: "Oswald", sans-serif; font-weight: 500; font-size: 22px;
    color: var(--band-green); letter-spacing: 0.3px;
  }
  .photo--hands {
    left: 86px; top: 428px; width: 126px; height: 92px;
    background: linear-gradient(180deg, var(--water) 0%, var(--skin) 45%, #d9a283 100%);
    border-radius: 30px 30px 14px 14px;
  }
</style>
</head>
<body>
  <section class="label label--front">
    <div class="brand-name">verdance</div>
    <div class="subtitle">Natural Handwash</div>
    <div class="photo photo--aloe-hands" role="img" aria-label="Photo of an aloe vera plant with water pouring into cupped hands"></div>
    <div class="claims">
      <span class="rule"></span>
      <div>99% ALOEBERA GEL</div>
      <div class="claim--green">PARABEN FREE</div>
      <span class="rule rule--wide"></span>
    </div>
    <div class="net-weight">NET WT 2.0Z (50g)</div>
  </section>

  <section class="label label--alt">
    <div class="photo photo--aloe-fan" role="img" aria-label="Photo of fanned aloe vera leaves with a cut leaf slice"></div>
    <div class="band"><span class="band-name">VERDANCE</span></div>
    <div class="alt-natural">Natural</div>
    <div class="alt-product">HAND WASH</div>
    <div class="photo photo--hands" role="img" aria-label="Photo of cupped hands under running water"></div>
  </section>
</body>
</html>
```